Varsity Purse Wordpress Website (re)design

we are a student run financial literacy website and are desperately trying to get college students to pay attention to the finances to create solid financial skills for life. This age group LOVES pixolette so instead of sharing a lot of text we want to tease through graphics/infographics topics that are relevant to them based on what their peers are discussing and then push them to our resources to learn more. ultimately we will also recommend products to them that are carefully selected by us. these will range from a book on paying back their student loan to a place to store their dorm stuff when they go home for summer break to a credit card we determine is best for them. So yes, commerce is imp but SEO to attract students comes first which we will do through survey monkey and cash prizes. we need to capture email address. we also have a "checklist" (attached and needs rebranding) of the basic and most imp money matters for them. Each item will hyperlink to our parnter, nuvoe, and need to do so seamlessly and push them back to us.

Target Market(s)

college students and young adults

Requirements
Must have
• simple, clean and graphic with an integration of survey monkey, an borvel store and a capture of emails through mailchimp or other similar. Ability to edit after ourselves on wordpress

```html
<!DOCTYPE html>
<html lang="en">
<head>
<meta charset="utf-8">
<title>Varsity Purse</title>
<link href="https://fonts.googleapis.com/css2?family=Arimo:wght@400;700&family=Lato:wght@400;700&display=swap" rel="stylesheet">
<style>
:root{
  --blue:#1b5e96;
  --blue-dark:#144a78;
  --green:#4ea535;
  --text:#444a50;
  --muted:#8b9096;
  --footer-bg:#f2f2f2;
  --white:#ffffff;
}
*{box-sizing:border-box;margin:0;padding:0}
html,body{width:1200px;height:3313px;overflow:hidden;background:var(--white)}
body{position:relative;font-family:"Lato",sans-serif;color:var(--text)}
.abs{position:absolute}
.head-font{font-family:"Arimo",sans-serif}

/* header */
.site-header{position:absolute;left:0;top:0;width:1200px;height:104px;background:var(--white)}
.brand{position:absolute;display:flex;align-items:center;gap:10px;font-family:"Lato",sans-serif;font-weight:700;color:var(--blue)}
.brand .dot{width:22px;height:22px;border-radius:50%;background:var(--green)}
.site-header .brand{left:134px;top:34px;font-size:34px}
.nav a{position:absolute;top:49px;font-family:"Arimo",sans-serif;font-weight:700;font-size:15px;color:#555a60;text-decoration:none}
.login{position:absolute;left:948px;top:39px;width:116px;height:38px;border-radius:19px;background:var(--blue);color:var(--white);font-family:"Arimo",sans-serif;font-weight:700;font-size:17px;display:flex;align-items:center;justify-content:center}

/* hero */
.hero{position:absolute;left:0;top:104px;width:1200px;height:690px;overflow:hidden}
.hero-photo{position:absolute;inset:0;background:linear-gradient(100deg,#5a3a22 0%,#7a5234 35%,#4a6a8e 62%,#7c8fa6 80%,#6b4a30 100%)}
.hero h1{position:absolute;left:154px;top:162px;font-family:"Arimo",sans-serif;font-weight:700;font-size:44px;line-height:42px;color:var(--white)}
.hero p{position:absolute;left:154px;top:260px;width:460px;font-family:"Arimo",sans-serif;font-size:19px;line-height:27px;color:var(--white)}
.hero .btn-outline{position:absolute;left:152px;top:333px;width:193px;height:56px;border:3px solid var(--white);border-radius:28px;color:var(--white);font-family:"Arimo",sans-serif;font-weight:700;font-size:18px;display:flex;align-items:center;justify-content:center}
.dots span{position:absolute;top:502px;width:16px;height:16px;border-radius:50%;border:2px solid var(--white)}
.dots span.on{background:var(--white)}
.hero svg{position:absolute;left:0;top:0}

/* about */
.checklist{position:absolute;left:184px;top:781px;width:351px;height:483px;background:linear-gradient(180deg,#cfe6f7 0%,#a9d6f3 60%,#b8dcf4 100%);border-top:4px solid var(--blue)}
.section-title{font-family:"Arimo",sans-serif;font-weight:700;color:var(--blue)}
.about-title{position:absolute;left:594px;top:788px;font-size:34px}
.about-text{position:absolute;left:595px;top:842px;width:425px;font-size:17px;line-height:27px;color:#4a4f55}
.feature{position:absolute;left:588px;width:440px}
.feature .ring{position:absolute;left:0;top:0;width:88px;height:88px;border-radius:50%;border:3px solid var(--green);display:flex;align-items:center;justify-content:center}
.feature h3{position:absolute;left:100px;top:18px;font-family:"Arimo",sans-serif;font-weight:700;font-size:17px;color:var(--blue);white-space:nowrap}
.feature p{position:absolute;left:102px;top:46px;width:330px;font-size:13.5px;line-height:19px;color:#4a4f55}
.btn-solid{position:absolute;height:49px;border-radius:25px;color:var(--white);font-family:"Arimo",sans-serif;font-weight:700;font-size:16px;display:flex;align-items:center;justify-content:center}
.btn-blue{background:var(--blue)}
.btn-green{background:var(--green)}

/* topic diagram */
.hub{position:absolute;left:193px;top:1443px;width:372px;height:372px;border-radius:50%;border:14px solid var(--green);background:var(--white);box-shadow:0 4px 12px rgba(0,0,0,.18);display:flex;align-items:center;justify-content:center}
.hub .brand{position:static;font-size:42px}
.hub .brand .dot{width:26px;height:26px}
.topic{position:absolute;height:130px;border-radius:0 65px 65px 0;color:var(--white)}
.topic.blue{background:var(--blue)}
.topic.green{background:var(--green)}
.topic .badge{position:absolute;left:-68px;top:-8px;width:146px;height:146px;border-radius:50%;background:var(--white);box-shadow:0 3px 10px rgba(0,0,0,.18);display:flex;align-items:center;justify-content:center}
.topic .badge i{display:flex;width:118px;height:118px;border-radius:50%;align-items:center;justify-content:center}
.topic.blue .badge i{background:var(--blue)}
.topic.green .badge i{background:var(--green)}
.topic h4{position:absolute;left:94px;font-family:"Arimo",sans-serif;font-weight:700;font-size:16px;line-height:18px}
.topic p{position:absolute;left:94px;width:180px;font-size:12.5px;line-height:18px}

/* why section */
.why-title{position:absolute;left:171px;top:2068px;font-family:"Arimo",sans-serif;font-weight:700;font-size:32px;line-height:35px;color:var(--white)}
.why-text{position:absolute;left:172px;top:2152px;width:430px;font-size:16.5px;line-height:25.5px;color:var(--white)}

/* testimonial */
.quote-title{position:absolute;left:0;width:1170px;top:2568px;text-align:center;font-family:"Arimo",sans-serif;font-weight:700;font-size:31px;color:#3d4247}
.quote-box{position:absolute;left:261px;top:2641px;width:647px;height:230px;border:3px solid var(--green);border-radius:62px;text-align:center}
.quote-mark{position:absolute;left:0;width:100%;top:14px;font-family:"Arimo",sans-serif;font-weight:700;font-size:64px;color:var(--blue);line-height:64px}
.quote-box p{position:absolute;left:40px;width:561px;top:76px;font-family:"Arimo",sans-serif;font-size:18px;line-height:25px;color:#55595e}
.quote-box .who{top:142px;font-weight:700;color:#3d4247}

/* footer */
.site-footer{position:absolute;left:0;top:2929px;width:1200px;height:384px;background:var(--footer-bg)}
.site-footer .brand{left:167px;top:120px;font-size:34px;color:#6b7076}
.site-footer .brand .dot{background:#9a9fa4}
.col{position:absolute;top:76px}
.col h5{font-family:"Arimo",sans-serif;font-weight:700;font-size:16px;color:var(--blue);margin-bottom:8px}
.col a{display:block;font-size:15px;line-height:24.5px;color:#4a4f55;text-decoration:none}
.social{position:absolute;top:104px;width:31px;height:31px;border-radius:50%;background:var(--blue)}
.rule{position:absolute;left:0;top:311px;width:1200px;height:1px;background:#cfd2d5}
.copyright{position:absolute;left:0;width:1200px;top:332px;text-align:center;font-size:14px;color:var(--muted)}
</style>
</head>
<body>

<header class="site-header">
  <div class="brand"><span>Varsity Purse</span><span class="dot"></span></div>
  <nav class="nav">
    <a style="left:402px">Take the Pledge</a>
    <a style="left:547px">Blog</a>
    <a style="left:611px">About Us</a>
    <a style="left:709px">Tips &amp; Tricks</a>
    <a style="left:831px">About nuvoe</a>
  </nav>
  <div class="login">Log In</div>
</header>

<section class="hero">
  <div class="hero-photo" role="img" aria-label="Student in a library holding a tablet with floating finance charts"></div>
  <h1>TAKE CHARGE OF<br>YOUR CHANGE</h1>
  <p>Lorem ipsum dolor sit amet consectetuer adipiscing elit Nam cursus Morbi ut mi Nullam enim leo</p>
  <div class="btn-outline">CLICK HERE</div>
  <div class="dots"><span style="left:567px"></span><span class="on" style="left:591px"></span><span style="left:617px"></span></div>
  <svg width="1200" height="690" viewBox="0 0 1200 690" aria-hidden="true">
    <path d="M0 640 Q560 540 1200 615 L1200 690 L0 690 Z" fill="var(--green)"/>
    <path d="M0 660 Q560 560 1200 640 L1200 690 L0 690 Z" fill="var(--white)"/>
    <path d="M0 662 Q560 562 1200 642" fill="none" stroke="var(--white)" stroke-width="0"/>
  </svg>
</section>

<section class="about">
  <div class="checklist" role="img" aria-label="Dorm Nest college money checklist infographic"></div>
  <h2 class="section-title about-title">ABOUT VARSITY PURSE</h2>
  <p class="about-text">Welcome to your FREE resource that will help you achieve financial independence and knowledge. Using peer-to-peer tips, personal stories and nuvoe, you can become a VarsityPurse!</p>
  <div class="feature" style="top:977px">
    <div class="ring"><svg width="50" height="50" viewBox="0 0 50 50"><circle cx="25" cy="25" r="23" fill="none" stroke="var(--blue)" stroke-width="2"/><path d="M15 26 L22 33 L36 18" fill="none" stroke="var(--blue)" stroke-width="2.5"/></svg></div>
    <h3>HOW TO GET STARTED</h3>
    <p>Varsity Purse’s roots go back to 2011 when Dana Whitfield, a CPA and Financial Planner</p>
  </div>
  <div class="feature" style="top:1090px">
    <div class="ring"><svg width="50" height="50" viewBox="0 0 50 50"><circle cx="25" cy="21" r="10" fill="none" stroke="var(--blue)" stroke-width="2"/><rect x="20" y="32" width="10" height="8" fill="none" stroke="var(--blue)" stroke-width="2"/></svg></div>
    <h3>WHO WE ARE</h3>
    <p>VPURSE believes that being knowledgeable about personal finances and landing a great job go</p>
  </div>
  <div class="btn-solid btn-blue" style="left:593px;top:1219px;width:167px">READ MORE</div>
</section>

<section class="topics">
  <svg class="abs" style="left:0;top:1420px" width="1200" height="420" viewBox="0 1420 1200 420" aria-hidden="true">
    <g fill="none" stroke="#8d9196" stroke-width="3">
      <path d="M493 1472 V1440 H563"/>
      <path d="M570 1630 H635"/>
      <path d="M493 1787 V1820 H561"/>
    </g>
    <g fill="var(--green)">
      <circle cx="564" cy="1440" r="9"/><circle cx="636" cy="1630" r="9"/><circle cx="561" cy="1820" r="9"/>
    </g>
  </svg>
  <div class="hub"><div class="brand"><span>Varsity Purse</span><span class="dot"></span></div></div>

  <div class="topic blue" style="left:661px;top:1380px;width:300px">
    <div class="badge"><i><svg width="60" height="60" viewBox="0 0 60 60"><circle cx="30" cy="30" r="20" fill="none" stroke="#fff" stroke-width="2.5"/><text x="30" y="39" text-anchor="middle" fill="#fff" font-family="Arimo" font-size="24" font-weight="700">$</text></svg></i></div>
    <h4 style="top:26px">HOW TO BUDGET</h4>
    <p style="top:50px">Having a solid budget is a fundamental building block in becoming financially</p>
  </div>
  <div class="topic green" style="left:727px;top:1556px;width:285px">
    <div class="badge"><i><svg width="60" height="60" viewBox="0 0 60 60"><g fill="none" stroke="#fff" stroke-width="2.5"><circle cx="18" cy="20" r="8"/><circle cx="42" cy="20" r="8"/><path d="M18 32 V50 M13 45 L18 50 L23 45 M42 32 V50 M37 45 L42 50 L47 45"/></g></svg></i></div>
    <h4 style="top:26px">MONEY SAVING HACKS<br>FOR MILLENNIALS</h4>
    <p style="top:70px">The other generations ove to pick on us, but the</p>
  </div>
  <div class="topic blue" style="left:666px;top:1730px;width:286px">
    <div class="badge"><i><svg width="60" height="60" viewBox="0 0 60 60"><g fill="none" stroke="#fff" stroke-width="2.5"><rect x="12" y="14" width="36" height="34"/><path d="M18 42 V34 M26 42 V28 M34 42 V31 M42 42 V24"/></g></svg></i></div>
    <h4 style="top:30px">HOW TO CREATE YOUR<br>OWN SIDE HUSTLE</h4>
    <p style="top:72px">So, you’re thinking of starting a side hustle, but before you do</p>
  </div>
</section>

<section class="why">
  <svg class="abs" style="left:0;top:1900px" width="1200" height="620" viewBox="0 1900 1200 620" role="img" aria-label="Hands typing on a laptop keyboard">
    <defs>
      <linearGradient id="whyFill" x1="0" y1="0" x2="1" y2="0">
        <stop offset="0" stop-color="var(--blue)"/>
        <stop offset="0.45" stop-color="#2a6aa0"/>
        <stop offset="0.7" stop-color="#6d7f92"/>
        <stop offset="1" stop-color="#3e5f86"/>
      </linearGradient>
    </defs>
    <path d="M0 1985 Q640 1870 1200 2010 L1200 2420 Q700 2560 0 2375 Z" fill="url(#whyFill)"/>
    <path d="M700 1935 Q1000 1960 1200 2035 L1200 2010 Q1000 1945 700 1935 Z" fill="var(--green)"/>
    <path d="M0 2380 Q300 2460 560 2470 Q260 2470 0 2400 Z" fill="var(--green)"/>
  </svg>
  <h2 class="why-title">WHY TAKE A PERSONAL<br>FINANCE COURSE?</h2>
  <p class="why-text">VarsityPurse will teach you how to use your student loan to get a new car,&nbsp; how to fill out those first day of work tax forms without calling mom and dad, and how to build credit without getting into credit card debt.</p>
  <div class="btn-solid btn-green" style="left:166px;top:2284px;width:162px;height:46px">READ MORE</div>
</section>

<section class="testimonials">
  <h2 class="quote-title">DON’T TAKE OUR WORD FOR IT…</h2>
  <svg class="abs" style="left:124px;top:2714px" width="30" height="50" viewBox="0 0 30 50" aria-hidden="true"><path d="M26 2 L4 25 L26 48" fill="none" stroke="#555" stroke-width="2"/></svg>
  <svg class="abs" style="left:1012px;top:2714px" width="30" height="50" viewBox="0 0 30 50" aria-hidden="true"><path d="M4 2 L26 25 L4 48" fill="none" stroke="#555" stroke-width="2"/></svg>
  <div class="quote-box">
    <div class="quote-mark">“</div>
    <p>Having personally practiced in the area of personal financial planning for over thirty years, I am thrilled that there is finally a tool that my kids can use to learn and understand this critical life-area.</p>
    <p class="who">Leo Hartman, Parent</p>
  </div>
</section>

<footer class="site-footer">
  <div class="brand"><span>Varsity Purse</span><span class="dot"></span></div>
  <div class="col" style="left:496px">
    <h5>COMPANY</h5>
    <a>Take the Pledge</a><a>Blog</a><a>About Us</a><a>Tips &amp; Tricks</a><a>About nuvoe</a>
  </div>
  <div class="col" style="left:679px">
    <h5>RESOURCES</h5>
    <a>Support</a><a>FAQ</a><a>Term of Use</a><a>Privacy Policy</a><a>Contact Us</a>
  </div>
  <div class="col" style="left:868px"><h5>FOLLOW US</h5></div>
  <span class="social" style="left:866px"></span>
  <span class="social" style="left:904px"></span>
  <span class="social" style="left:943px"></span>
  <span class="social" style="left:982px"></span>
  <div class="rule"></div>
  <p class="copyright">Copyright © 2019 All right reserved</p>
</footer>

</body>
</html>
```